PYLON SIGN FOR “MEADOWLARK CAR WASH SPRINT”

please see the new images in my brief. I have a logo design and the colors I would like you to follow.

please put "meadowlark car wash sprint" in the logo

Target Market(s)

GENERAL PUBLIC

Industry/Entity Type

CAR WASH

Font styles to use
Other font styles liked:
• CURSIVE AND BLOCK LETTERING BOTH AS IN THE SAMPLE PIC

Colors
00AB8E
00BBA5
67D7C9
C6EFE9
E9F9F6
6B429C
8869AF
B7A5CE
E3DAEB
F3F0F8

Requirements
Must have
• 1. “MEADOWLARK CAR WASH SPRINT” PLEASE PUT THIS IN THE LOGO 2. USE BLACK, WHITE, GREEN AND SILVER FOR A COLOR
Nice to have
• I WOULD LIKE TO SEE THE SIGN IN BOTH COLOR THEMES: WHITE, BLACK, GREEN AND SILVER AND WHITE BLACK PURPLE AND SILVER

```html
<!DOCTYPE html>
<html lang="en">
<head>
<meta charset="utf-8">
<title>Meadowlark Car Wash Sprint – Pylon Sign Colour Themes</title>
<link href="https://fonts.googleapis.com/css2?family=Gloock&display=swap" rel="stylesheet">
<style>
  :root {
    --board-bg: #222222;
    --sign-bg: #ffffff;
    --silver: #7b7b77;
    --purple-ink: #4a2480;
    --green-ink: #0b3b24;
    --water-deep: #4f8fbf;
    --water-mid: #a9d3ec;
    --water-light: #e6f3fb;
  }
  * { margin: 0; padding: 0; box-sizing: border-box; }
  html, body {
    width: 1200px;
    height: 1200px;
    overflow: hidden;
    background: var(--board-bg);
  }
  .board {
    position: relative;
    width: 1200px;
    height: 1200px;
  }
  .sign {
    position: absolute;
    left: 132px;
    width: 936px;
    height: 467px;
    background: var(--sign-bg);
    overflow: hidden;
  }
  .sign--purple { top: 53px; --ink: var(--purple-ink); }
  .sign--green  { top: 572px; --ink: var(--green-ink); }

  .sign__water {
    position: absolute;
    left: 0;
    bottom: 0;
    width: 100%;
    height: 200px;
    display: block;
  }

  .brand__dot {
    position: absolute;
    left: 62px;
    top: 104px;
    width: 176px;
    height: 176px;
    border-radius: 50%;
    background: var(--ink);
  }
  .brand__name {
    position: absolute;
    left: 278px;
    top: 92px;
    font-family: "Gloock", serif;
    font-weight: 400;
    color: var(--silver);
    line-height: 1;
  }
  .brand__line {
    display: block;
    white-space: nowrap;
  }
  .brand__line--main {
    font-size: 104px;
    letter-spacing: 0;
  }
  .brand__line--sub {
    font-size: 46px;
    letter-spacing: 2px;
    text-transform: uppercase;
    margin-top: 14px;
  }
</style>
</head>
<body>
  <main class="board">
    <section class="sign sign--purple" aria-label="Pylon sign, white, black, purple and silver theme">
      <svg class="sign__water" role="img" aria-label="Blue water splash with droplets across the lower edge of the sign" viewBox="0 0 936 200" preserveAspectRatio="none">
        <defs>
          <linearGradient id="water-purple" x1="0" y1="0" x2="0" y2="1">
            <stop offset="0" stop-color="var(--water-light)" stop-opacity="0"/>
            <stop offset="0.4" stop-color="var(--water-mid)"/>
            <stop offset="1" stop-color="var(--water-deep)"/>
          </linearGradient>
        </defs>
        <rect x="0" y="0" width="936" height="200" fill="url(#water-purple)"/>
      </svg>
      <span class="brand__dot" aria-hidden="true"></span>
      <h1 class="brand__name">
        <span class="brand__line brand__line--main">Meadowlark</span>
        <span class="brand__line brand__line--sub">Car Wash Sprint</span>
      </h1>
    </section>

    <section class="sign sign--green" aria-label="Pylon sign, white, black, green and silver theme">
      <svg class="sign__water" role="img" aria-label="Blue water splash with droplets across the lower edge of the sign" viewBox="0 0 936 200" preserveAspectRatio="none">
        <defs>
          <linearGradient id="water-green" x1="0" y1="0" x2="0" y2="1">
            <stop offset="0" stop-color="var(--water-light)" stop-opacity="0"/>
            <stop offset="0.4" stop-color="var(--water-mid)"/>
            <stop offset="1" stop-color="var(--water-deep)"/>
          </linearGradient>
        </defs>
        <rect x="0" y="0" width="936" height="200" fill="url(#water-green)"/>
      </svg>
      <span class="brand__dot" aria-hidden="true"></span>
      <h2 class="brand__name">
        <span class="brand__line brand__line--main">Meadowlark</span>
        <span class="brand__line brand__line--sub">Car Wash Sprint</span>
      </h2>
    </section>
  </main>
</body>
</html>
```